Dental Medical History Form - Content provided

Design a medical history form for a dental practice. Content is provided so all that is needed is the formatting to make it look great and easy to read.

"Patient Information" to include all information contained in top portion of the "Patient Medical History Form" docx file.

"Medical History" should follow the formatting and content of the "Exact Medical History" file as this is what the entry fields look like in our practice software and so we would like it to match.

1st page - Patient info, allergies, medications, antibiotics, joint replacement, pregnancy.

2nd page - Do you have, or have you had, any of the following? . . . . . . .
Updates

Target Market(s)

All ages but must be clear enough for elderly to read. Use as much space as possible to keep font size bigger yet keep to two pages

Industry/Entity Type

Dental

Font styles to use
Sans Serif

Requirements
Must have
• All content provided
• Our logo at the top (file provided)
• Century Gothic Font
• Limit to two pages

```html
<!DOCTYPE html>
<html lang="en">
<head>
<meta charset="utf-8">
<title>Harbourline Dental – Confidential Medical History</title>
<link rel="stylesheet" href="https://fonts.googleapis.com/css2?family=PT+Sans+Narrow:wght@400;700&display=swap">
<style>
:root{
  --bg:#6fcbe8;
  --paper:#ffffff;
  --navy:#1b4c98;
  --blue:#2b7fc6;
  --ink:#1f3f6e;
  --rule:#b9e1f2;
  --box:#9fd3ea;
  --grey:#4a4f57;
}
*{box-sizing:border-box;margin:0;padding:0}
html,body{width:1200px;height:784px;overflow:hidden;background:var(--bg)}
body{font-family:"PT Sans Narrow",Arial Narrow,sans-serif;color:var(--ink);font-size:11px}
.form-page{position:absolute;left:318px;top:10px;width:564px;height:764px;background:var(--paper);
  box-shadow:0 6px 18px rgba(0,60,100,.25);overflow:hidden}
.bottom-stripe{position:absolute;left:0;right:0;bottom:0;height:10px;background:linear-gradient(90deg,var(--navy),var(--blue))}
.turnover-tab{position:absolute;left:22px;bottom:10px;background:linear-gradient(90deg,var(--blue),var(--navy));
  color:#fff;font-weight:700;font-size:12px;padding:5px 18px;border-radius:6px 6px 0 0}
.header{position:absolute;left:28px;top:20px;right:28px;height:64px}
.brand-name{font-size:26px;color:var(--grey);letter-spacing:.5px;display:flex;align-items:center;gap:8px}
.brand-name .dot{width:12px;height:12px;border:2px solid var(--grey)}
.contact{position:absolute;right:0;top:4px;text-align:right;font-weight:700;font-size:10.5px;color:var(--navy);line-height:1.3}
.contact .phone{font-size:12px;display:flex;align-items:center;justify-content:flex-end;gap:5px}
.title-band{position:absolute;left:150px;right:28px;top:74px;height:16px;
  background:linear-gradient(90deg,var(--navy),var(--blue) 70%,rgba(43,127,198,0));
  color:#fff;font-weight:700;font-size:10px;letter-spacing:3px;padding:2px 12px}
.content{position:absolute;left:28px;right:28px;top:98px}
.row{display:flex;align-items:flex-end;gap:6px;height:19px}
.label{white-space:nowrap}
.line{flex:1;border-bottom:1px solid var(--rule);height:14px;position:relative}
.line small{position:absolute;left:2px;top:-1px;font-size:9px;color:var(--ink)}
.box{display:inline-block;flex:none;width:9px;height:9px;border:1px solid var(--box);vertical-align:middle;margin:0 6px 0 3px}
.section-tag{display:inline-block;margin:8px 0 3px;padding:2px 40px 2px 8px;font-weight:700;color:#fff;font-size:11px;
  background:linear-gradient(90deg,var(--navy),var(--blue) 70%,rgba(43,127,198,0))}
.checks{display:grid;grid-template-columns:repeat(6,auto);justify-content:space-between;row-gap:5px;padding:2px 0}
.check{display:flex;align-items:center;white-space:nowrap}
.check .box{margin:0 0 0 4px}
.dark-line{border-bottom:1px solid var(--navy);height:19px}
.q{display:flex;align-items:center;height:20px;gap:4px}
.q .label{width:190px}
</style>
</head>
<body>
<main class="form-page">
  <header class="header">
    <div class="brand-name"><span>Harbourline Dental</span><span class="dot"></span></div>
    <div class="contact">
      <div class="phone">
        <svg width="14" height="14" viewBox="0 0 14 14" aria-hidden="true"><rect width="14" height="14" rx="3" fill="#2b7fc6"/><path d="M4.5 3.2l1.3 1.6-.8 1c.6 1.2 1.4 2 2.6 2.6l1-.8 1.6 1.3-.7 1.3C6.6 10 4 7.4 3.8 4z" fill="#fff"/></svg>
        (02) 4000 1234
      </div>
      <div>Harbourline Dental, Suite 4, 18 Example Rd,</div>
      <div>Seaview NSW 2000</div>
    </div>
  </header>
  <div class="title-band">CONFIDENTIAL MEDICAL HISTORY</div>

  <section class="content">
    <div class="row"><span class="label">Name:</span><span class="line"><small>First</small></span><span class="line"><small>Middle</small></span><span class="line"><small>Last</small></span></div>
    <div class="row"><span class="label">Address:</span><span class="line"></span></div>
    <div class="row"><span class="label">DOB:</span><span class="line"></span><span class="label">Email Address:</span><span class="line" style="flex:2"></span></div>
    <div class="row"><span class="label">Phone Number(s): Mobile</span><span class="line"></span><span class="label">Work</span><span class="line"></span><span class="label">Home</span><span class="line"></span></div>
    <div class="row"><span class="label">Emergency Contact Person: Name:</span><span class="line"></span><span class="label">Relationship:</span><span class="line"></span><span class="label">Phone number:</span><span class="line"></span></div>

    <div class="section-tag">General Practitioner:</div>
    <div class="row"><span class="label">Name:</span><span class="line"></span></div>
    <div class="row"><span class="label">Practice Name:</span><span class="line"></span><span class="label">Phone Number:</span><span class="line"></span></div>
    <div class="row"><span class="label">Do you have a health fund with dental cover? Yes<span class="box"></span>or No<span class="box"></span>If so, what is the name of the fund?</span><span class="line"></span></div>
    <div class="row"><span class="label">Fund Number?</span><span class="line"></span><span class="label">Priority Number on card: 0<span class="box"></span>1<span class="box"></span>2<span class="box"></span>3<span class="box"></span>4<span class="box"></span>5<span class="box"></span></span></div>
    <div class="row"><span class="label">Occupation:</span><span class="line"></span><span class="label">Referred by:</span><span class="line"></span></div>

    <div class="section-tag">Please indicate if you are allergic to any of the following?:</div>
    <div class="checks">
      <span class="check">Aspirin<span class="box"></span></span>
      <span class="check">Codeine<span class="box"></span></span>
      <span class="check">Penicillin<span class="box"></span></span>
      <span class="check">Sulfites<span class="box"></span></span>
      <span class="check">Latex<span class="box"></span></span>
      <span class="check">Local Anaesthetic<span class="box"></span></span>
      <span class="check">Lactose<span class="box"></span></span>
      <span class="check">Nickel<span class="box"></span></span>
    </div>
    <div class="row"><span class="label">Other:</span><span class="line"></span></div>

    <div class="section-tag">Are you currently taking, or have ever taken, any of the following medication?:</div>
    <div class="checks">
      <span class="check">Asthma inhaler<span class="box"></span></span>
      <span class="check">Anti-epileptics<span class="box"></span></span>
      <span class="check">Anti-depressants<span class="box"></span></span>
      <span class="check">Blood Pressure<span class="box"></span></span>
      <span class="check">Blood Thinners<span class="box"></span></span>
      <span class="check">Bisphosphonates<span class="box"></span></span>
      <span class="check">Chemotherapy<span class="box"></span></span>
      <span class="check">Insulin<span class="box"></span></span>
      <span class="check">Immunosuppressants<span class="box"></span></span>
      <span class="check">Steroids<span class="box"></span></span>
      <span class="check">Oral Contraceptive<span class="box"></span></span>
      <span class="check">Other<span class="box"></span></span>
    </div>

    <div class="section-tag">Please specify medication name, dose, and frequency where possible:</div>
    <div class="dark-line"></div>
    <div class="dark-line"></div>
    <div class="dark-line"></div>
    <div class="dark-line" style="margin-bottom:8px"></div>

    <div class="q"><span class="label">Do you require antibiotic cover?</span>Yes<span class="box"></span>No<span class="box"></span></div>
    <div class="q"><span class="label">Have you had a joint replacement?</span>Yes<span class="box"></span>No<span class="box"></span></div>
    <div class="q"><span class="label">Women: &nbsp;Are you pregnant?</span>Yes<span class="box"></span>No<span class="box"></span>Possible<span class="box"></span>or &nbsp;Breast Feeding?&nbsp; Yes<span class="box"></span>No<span class="box"></span></div>
  </section>

  <div class="turnover-tab">Please Turnover</div>
  <div class="bottom-stripe"></div>
</main>
</body>
</html>
```